Elevating our current Business Card Design

We want to elevate our current business card with a new design to look like a zenith 300 company. We are a premium lubricant distributor (oil and grease).
We need 2 versions, version 1 is as per the uploaded a copy of our current business card with the English version.
For our Chinese version we need to use the front to be English in English and have the back of the card designed exactly like the front for all info to be in Chinese.
The design template needs to be such that we can amend the template with adding different information for each person's card.
The background colour of the card can be changed- we just need to clearly see all information on the card and logos.
The QJR and Ember steady logos cannot have any colour or display changes- only use the logos attached.
All logos need to be included and all information from the attached current card

```html
<!DOCTYPE html>
<html lang="en">
<head>
<meta charset="utf-8">
<title>Veltra Business Card</title>
<link href="https://fonts.googleapis.com/css2?family=Open+Sans:wght@400;600;700;800&display=swap" rel="stylesheet">
<style>
  :root{
    --stage:#232323;
    --card:#1c1c1e;
    --red:#e8302a;
    --red-deep:#c21f2b;
    --gold:#f0b12c;
    --white:#ffffff;
    --grey:#9a9a9e;
    --orange:#f07a22;
    --green:#1f5e35;
  }
  *{margin:0;padding:0;box-sizing:border-box}
  html,body{width:1200px;height:780px;overflow:hidden;background:var(--stage)}
  body{font-family:"Open Sans",Arial,sans-serif;position:relative}
  .card{position:absolute;top:230px;width:560px;height:320px;background:var(--card);
    border-radius:4px;box-shadow:0 14px 30px rgba(0,0,0,.55);overflow:hidden}
  .card--front{left:30px}
  .card--back{left:610px}

  .brand{display:flex;align-items:center;gap:14px;position:absolute}
  .brand__dot{background:var(--gold);border-radius:50%}
  .brand__name{color:var(--red);font-weight:800;letter-spacing:2px;line-height:1}
  .card--front .brand{left:50%;top:50%;transform:translate(-50%,-50%)}
  .card--front .brand__dot{width:44px;height:44px}
  .card--front .brand__name{font-size:76px}
  .card--back .brand--top{right:38px;top:30px}
  .card--back .brand--top .brand__dot{width:24px;height:24px}
  .card--back .brand--top .brand__name{font-size:42px}

  .person{position:absolute;left:74px;top:40px}
  .person__name{color:var(--red);font-weight:700;font-size:28px;line-height:1.05}
  .person__role{color:var(--white);font-size:13px;font-weight:600;letter-spacing:.3px}

  .timeline{position:absolute;left:0;top:0}
  .contacts{position:absolute;left:70px;top:118px;list-style:none;color:var(--white);font-size:13.5px;line-height:22px}
  .contacts li{height:22px}
  .address{position:absolute;left:70px;top:262px;color:var(--white);font-size:13.5px;line-height:18px;white-space:nowrap}

  .badges{position:absolute;right:36px;top:178px;display:flex;gap:14px;align-items:flex-end}
  .badge{width:40px;height:40px;border-radius:50%;background:var(--orange);border:4px solid var(--grey)}
  .badge--eco{width:46px;height:34px;border-radius:8px;background:var(--green);border:none}

  .partner-strip{position:absolute;right:20px;bottom:26px;display:flex;height:44px}
  .partner-strip__own{border:2px solid var(--red);border-right:none;display:flex;align-items:center;gap:6px;padding:0 8px;border-radius:4px 0 0 4px}
  .partner-strip__own .brand__name{font-size:17px;font-weight:800;color:var(--red);letter-spacing:1.5px}
  .partner-strip__own small{color:var(--red);font-size:7px;font-weight:600;line-height:1.15;text-transform:uppercase;display:block;width:64px}
  .partner-strip__ally{background:var(--red);color:var(--white);padding:6px 10px;border-radius:0 4px 4px 0;display:flex;flex-direction:column;justify-content:center}
  .partner-strip__ally strong{font-size:15px;font-weight:800;letter-spacing:1px;line-height:1}
  .partner-strip__ally span{font-size:6.5px;font-weight:600;letter-spacing:.6px}
</style>
</head>
<body>

<section class="card card--front" aria-label="Card front">
  <div class="brand">
    <span class="brand__dot"></span>
    <span class="brand__name">VELTRA</span>
  </div>
</section>

<section class="card card--back" aria-label="Card back">
  <div class="brand brand--top">
    <span class="brand__dot"></span>
    <span class="brand__name">VELTRA</span>
  </div>

  <svg class="timeline" width="70" height="320" viewBox="0 0 70 320" aria-hidden="true">
    <line x1="38" y1="20" x2="38" y2="310" stroke="var(--red-deep)" stroke-width="1.5"/>
    <g transform="translate(38 62)">
      <rect x="-17" y="-17" width="34" height="34" transform="rotate(45)" fill="var(--red-deep)"/>
      <circle cx="0" cy="-6" r="5" fill="#fff"/>
      <path d="M-10 10 Q0 -4 10 10 Z" fill="#fff"/>
    </g>
    <g fill="var(--red-deep)" stroke="#fff" stroke-width="1.2">
      <g transform="translate(38 129)"><rect x="-8" y="-8" width="16" height="16" transform="rotate(45)"/><path d="M-3 -3 q1 4 6 6 l1-2 -2-1 -1 1 q-2-1 -3-3 l1-1 -1-2z" fill="#fff" stroke="none"/></g>
      <g transform="translate(38 151)"><rect x="-8" y="-8" width="16" height="16" transform="rotate(45)"/><rect x="-2.5" y="-4" width="5" height="8" rx="1" fill="none"/></g>
      <g transform="translate(38 173)"><rect x="-8" y="-8" width="16" height="16" transform="rotate(45)"/><rect x="-4" y="-2" width="8" height="5" fill="none"/><line x1="-2" y1="-4" x2="2" y2="-4"/></g>
      <g transform="translate(38 195)"><rect x="-8" y="-8" width="16" height="16" transform="rotate(45)"/><circle r="4" fill="none"/><line x1="-4" y1="0" x2="4" y2="0"/></g>
      <g transform="translate(38 217)"><rect x="-8" y="-8" width="16" height="16" transform="rotate(45)"/><rect x="-4" y="-3" width="8" height="6" fill="none"/><path d="M-4 -3 L0 0 L4 -3" fill="none"/></g>
      <g transform="translate(38 272)"><rect x="-8" y="-8" width="16" height="16" transform="rotate(45)"/><path d="M0 4 L-3 -1 A3.5 3.5 0 1 1 3 -1 Z" fill="none"/></g>
    </g>
  </svg>

  <div class="person">
    <div class="person__name">Mara Quinlan</div>
    <div class="person__role">Administration Executive</div>
  </div>

  <ul class="contacts">
    <li>1300 472 615</li>
    <li>+61 400 218 904</li>
    <li>+61 8 9000 4512</li>
    <li>www.veltradirect.com</li>
    <li>mara.quinlan@veltradirect.com</li>
  </ul>

  <div class="address">48 Harbour Freight Way<br>Millbrook, WA 6199</div>

  <div class="badges">
    <span class="badge badge--eco" role="img" aria-label="Ember steady certification badge"></span>
    <span class="badge" role="img" aria-label="QJR safety certification badge"></span>
    <span class="badge" role="img" aria-label="QJR quality certification badge"></span>
    <span class="badge" role="img" aria-label="QJR environmental certification badge"></span>
  </div>

  <div class="partner-strip">
    <div class="partner-strip__own">
      <span class="brand__name">VELTRA</span>
      <small>Veltra Lubricant Distributors</small>
    </div>
    <div class="partner-strip__ally">
      <strong>NORVANE</strong>
      <span>PREMIUM LUBRICANTS</span>
    </div>
  </div>
</section>

</body>
</html>
```